Landing Page für B2B-Softwareentwicklungsfirma
Zielgruppe
Wir sind eine (relativ kleine) B2B Softwareentwicklungsfirma, die Software zum Wetten auf Pferderennen erstellt.
Unsere Kunden sind Buchmacher und Rennbahnbetreiber.
Unsere Software läuft auf verschiedener Hardware (Touchscreen Terminals, Handy, Kassa, Webseite,...) und wird teilweise von Endkunden (Sportwetter) als auch Kunden-Mitarbeitern verwendet.
Was uns von anderen Softwarefirmen in diesem Bereich unterscheidet ist:
- Wir sind extrem verlässlich und unsere Software läuft störungsfrei
- Wir haben extrem viel Knowhow und ein großes Netzwerk im Bereich Pferdesport/-wetten
- Wir sind flexibel, gehen auf Kundenwünsche immer schnell und kosteneffizient ein
- Unsere softwaretechnischen Fähigkeiten sind ausgezeichnet (wir sind hauptsächlich Programmierer - weniger Businessleute).
- Wir sind für unsere Kunden immer persönlich, direkt und einfach ansprechbar (kleine Firma)
- Wir sind seit ca 15 Jahren erfolgreich im Markt, und auch Marktführer im deutschsprachigen Raum
- Wir haben ein sehr breites Produktportfolio (Terminal, Kassa, Mobile Webseite, Desktop Webseite, Backoffice, Risk Management)
- Wir legen viel Wert auf sauberes und auch modernes UI/UX-Design
Wir benötigen nun einen professionellen Webauftritt um in neue Märkte einzutreten.
Als ersten Schritt möchten wir gerne eine Single-Page Landingpage, die alle wichtigen Punkte im Überblick darstellt.
Aufgabenstellung
Das Design soll die Punkte aus der obigen Beschreibung über uns widerspiegeln, und auch unsere Werte:
Wichtig: Modern, Verlässlichkeit, Dynamisch, Kosteneffizient, Freundlich
Optional: Kreativ, Flexibilität
Wichtig ist auch der Bezug zum Pferderennsport!
Und dass wir eine B2B Softwarefirma sind!
Bitte beachten Sie unser neues Firmenlogo - siehe Anhang.
Die Landingpage soll eher hell, klar, offen, freundlich, sachlich sein.
Die Landingpage soll auf Mobile und Desktop funktionieren und gut aussehen.
Bitte verwenden Sie folgende Gliederung der Landingpage:
Sections:
....* Above the fold
........headline: horse betting software
........subheadline: Multi-product betting solution for bookmakers and racetrack operators.
................................Software production for land-based operations and online betting.
........call-to-action: get in touch
........secondary call-to-action: view products
........switch language
........links to other sections
....* Products
........Point of Sale
............Title: Quick and streamlined bet placement
............Short desc: Optimized bet placement solution for your bet shops and race tracks. Supports Windows-based touchscreen terminals and many different printers and scanners out of the box.
........Self-Service Terminals
............Title: Let users take control
............Short desc: Easy to use touchscreen software for new and professional punters. Running on any Windows-based hardware and adapted to your special needs.
........Web and Mobile Betting
............Title: Reach your target audience wherever they are
............Short desc: Allow your customers to enter their bets on any desktop or mobile browser.
........Bet Management
............Title: Stay in control of your meetings and bets
............Short desc: Browser-based Back-Office solution to control all your meetings,..

```html
<!DOCTYPE html>
<html lang="en">
<head>
<meta charset="utf-8">
<title>quellnet – Horse Betting Software</title>
<link href="https://fonts.googleapis.com/css2?family=Poppins:wght@400;500;600;700&display=swap" rel="stylesheet">
<style>
:root{
  --navy:#1e3448;
  --brand:#0d5a8c;
  --cyan:#3cc8e8;
  --hero-bg:#f3f3f6;
  --page-bg:#fafafc;
  --text:#2b3440;
  --muted:#4a5563;
  --line:#ececf1;
}
*{box-sizing:border-box;margin:0;padding:0}
html,body{width:671px;height:1200px;overflow:hidden}
body{font-family:'Poppins',sans-serif;background:var(--page-bg);color:var(--text);position:relative}
.abs{position:absolute}
.hero{position:absolute;left:0;top:0;width:671px;height:383px;background:var(--hero-bg)}
.logo{left:93px;top:17px;font-size:13px;font-weight:600;color:var(--navy);letter-spacing:1.5px;display:flex;align-items:center;gap:5px}
.logo-dot{width:7px;height:7px;border-radius:50%;background:var(--cyan)}
.nav a{position:absolute;top:20px;font-size:7px;color:var(--navy);text-decoration:none}
.btn{position:absolute;background:var(--brand);color:#fff;font-size:7px;font-weight:500;border-radius:3px;display:flex;align-items:center;justify-content:center;box-shadow:0 2px 4px rgba(13,90,140,.25)}
.eyebrow{font-size:7px;font-weight:500;letter-spacing:.8px;color:var(--cyan)}
.hero-title{left:85px;top:112px;font-size:25px;line-height:28px;font-weight:700;color:var(--navy)}
.hero-copy{left:85px;top:208px;width:220px;font-size:7.6px;line-height:13.5px;color:var(--text)}
.link{left:190px;top:288px;font-size:7px;color:var(--brand);text-decoration:underline}
.hero-visual{left:326px;top:113px;width:250px;height:185px}
.sec-head{left:0;width:671px;text-align:center}
.sec-title{font-size:20px;font-weight:700;color:var(--navy)}
.sec-copy{font-size:7.5px;line-height:12.5px;color:var(--text)}
.prod-title{font-size:13.5px;font-weight:600;color:var(--navy)}
.prod-copy{width:240px;font-size:7.6px;line-height:12.5px;color:var(--text)}
.card{position:absolute;width:72px;height:55px;background:#fff;border-radius:3px;box-shadow:0 2px 5px rgba(0,0,0,.08);display:flex;flex-direction:column;align-items:center;justify-content:center;gap:5px;font-size:7.5px;color:var(--text)}
.shot{position:absolute;border-radius:4px;box-shadow:0 2px 6px rgba(0,0,0,.18)}
.dots{position:absolute;display:flex;gap:5px}
.dots span{width:5px;height:5px;border-radius:50%;background:#e6e6ec}
.dots span:first-child{background:var(--navy)}
.divider{position:absolute;height:1px;background:var(--line)}
</style>
</head>
<body>
<section class="hero">
  <div class="abs logo"><span class="logo-dot"></span>QUELLNET</div>
  <nav class="nav">
    <a style="left:236px">Products ⌄</a>
    <a style="left:283px">Why us?</a>
    <a style="left:328px">Company &amp; Team</a>
    <a style="left:405px">FAQ</a>
    <a style="left:492px">DE / EN</a>
  </nav>
  <div class="btn" style="left:535px;top:15px;width:44px;height:20px">Contact</div>

  <p class="abs eyebrow" style="left:85px;top:95px">HORSE BETTING SOFTWARE PROVIDERS</p>
  <h1 class="abs hero-title">The Reliable Way<br>To Manage<br>Your Horse Races</h1>
  <p class="abs hero-copy">We provide multi-product betting solutions for bookmakers and racetrack operators.<br>Our proven software products are a perfect fit for land-based as well as online betting operations.</p>
  <div class="btn" style="left:85px;top:281px;width:89px;height:23px">View our products</div>
  <a class="abs link">Get in touch</a>

  <svg class="abs hero-visual" viewBox="0 0 250 185" role="img" aria-label="Galloping racehorse with jockey in front of a betting terminal screen on a cyan circle">
    <circle cx="112" cy="87" r="93" fill="#3cc8e8"/>
    <rect x="95" y="12" width="148" height="78" rx="3" fill="#2b3a4c"/>
    <ellipse cx="95" cy="100" rx="90" ry="60" fill="#3a3f45" opacity=".85"/>
  </svg>
</section>

<div class="sec-head abs" style="top:428px"><p class="eyebrow">BETTING SOLUTIONS</p></div>
<div class="sec-head abs" style="top:444px"><h2 class="sec-title">Our Products</h2></div>
<div class="sec-head abs" style="top:481px"><p class="sec-copy">Neque egestas congue quisque egestas diam in. Semper quis<br>lectus nulla at volutpat diam ut venenatis.</p></div>

<h3 class="abs prod-title" style="left:90px;top:577px">Point of Sale</h3>
<p class="abs prod-copy" style="left:90px;top:607px">Lorem ipsum dolor sit amet, consectetur adipiscing elit, sed do eiusmod tempor incididunt ut labore et dolore magna aliqua.</p>
<div class="card" style="left:94px;top:647px">
  <svg width="18" height="18" viewBox="0 0 18 18"><circle cx="9" cy="9" r="8" fill="#5cc48a"/><path d="M5 9l3 3 5-6" stroke="#fff" stroke-width="2" fill="none"/></svg>100% reliable</div>
<div class="card" style="left:174px;top:647px">
  <svg width="18" height="18" viewBox="0 0 18 18"><rect x="3" y="8" width="4" height="8" rx="1" fill="#f59a6b"/><path d="M8 8l3-6c2 0 2 2 1.5 4H16v9H8z" fill="#f7b08a"/></svg>Easy to use</div>
<div class="card" style="left:253px;top:647px">
  <svg width="20" height="18" viewBox="0 0 20 18"><path d="M2 15a8 8 0 0 1 16 0" stroke="#f39a2f" stroke-width="3" fill="none"/><path d="M10 15l6-8" stroke="#3c7fc8" stroke-width="2"/></svg>Performant</div>
<div class="btn" style="left:90px;top:718px;width:89px;height:23px">More information</div>
<div class="shot" style="left:349px;top:579px;width:224px;height:145px;background:linear-gradient(90deg,#dde3ea 0 20%,#f7f8fa 20%)" role="img" aria-label="Back-office screenshot with race starters table"></div>
<div class="dots" style="left:449px;top:736px"><span></span><span></span><span></span></div>

<div class="divider" style="left:90px;top:777px;width:490px"></div>

<div class="shot" style="left:98px;top:856px;width:223px;height:119px;background:linear-gradient(180deg,#2b3a4c,#1f2a38)" role="img" aria-label="Self-service terminal betting screen screenshot"></div>
<div class="dots" style="left:197px;top:987px"><span></span><span></span><span></span></div>
<h3 class="abs prod-title" style="left:342px;top:839px">Self-Service Terminals</h3>
<p class="abs prod-copy" style="left:342px;top:869px">Lorem ipsum dolor sit amet, consectetur adipiscing elit, sed do eiusmod tempor incididunt ut labore et dolore magna aliqua.</p>
<div class="card" style="left:346px;top:909px">
  <svg width="18" height="18" viewBox="0 0 18 18"><circle cx="9" cy="9" r="8" fill="#5cc48a"/><path d="M5 9l3 3 5-6" stroke="#fff" stroke-width="2" fill="none"/></svg>100% reliable</div>
<div class="card" style="left:426px;top:909px">
  <svg width="18" height="18" viewBox="0 0 18 18"><rect x="3" y="8" width="4" height="8" rx="1" fill="#f59a6b"/><path d="M8 8l3-6c2 0 2 2 1.5 4H16v9H8z" fill="#f7b08a"/></svg>Easy to use</div>
<div class="card" style="left:505px;top:909px">
  <svg width="20" height="18" viewBox="0 0 20 18"><path d="M2 15a8 8 0 0 1 16 0" stroke="#f39a2f" stroke-width="3" fill="none"/><path d="M10 15l6-8" stroke="#3c7fc8" stroke-width="2"/></svg>Performant</div>
<div class="btn" style="left:342px;top:984px;width:89px;height:23px">More information</div>

<div class="divider" style="left:85px;top:1061px;width:490px"></div>
</body>
</html>
```